Healthcare/Medical Consultant Company

QRN is a Healthcare Conultant Company. We help doctors manage the business side of their medical practice.
We already have a very basic world press design. We want an upgraded design that conveys partnership, healthcare expertise and healthcare innovation to our client. It needs to have a sleek, clean, modern and inclusive look. Pictures need need to convey diversity (including pictures of people of all races and shows both men and women working together in a healthcare environment to make it better). The Pictures on the home page should particularly illustrate diversity and Healthcare expertise. The company logo is blue and white but the site doesn’t have to follow the exact same theme but the logo needs to blend well with the chosen theme. The logo should ideally be in the header of the website. We would also like the following included in our website:

1. Pages should include: a home page, About Us page, Services page, Get a quote page, Contact Us page, Staff page(where we can add pictures and bio for staff).

2. The Drop down menu for services should have hyperlinks ( for each service)Leading to a page that provides detailed info about that specific service. Our services include: Revenue Cycle Management, Regulatory Compliance, Human Resources Management, & practice Management.

3. Links to social media should in the header or footer of each page.

4. Contact info should be in the footer of each page.

5. Clients should be an email to us from the contact page.

Target Market(s)

Physician Medical Practices

Industry/Entity Type

Medical

Coding

Coded - Design and coding required

Font styles to use
Sans Serif

Colors

Designer to choose colors to be used in the design.

Requirements
Must have
• See project description
Nice to have
• See project description

```html
<!DOCTYPE html>
<html lang="en">
<head>
<meta charset="utf-8">
<title>QRN – Quorra Health Network LLC</title>
<link href="https://fonts.googleapis.com/css2?family=Open+Sans:wght@400;600;700&family=Marcellus&family=Montserrat:wght@500;700;800&display=swap" rel="stylesheet">
<style>
:root{
  --blue:#1a5fb4;
  --blue-dark:#0f3f86;
  --blue-deep:#0a2f6a;
  --blue-light:#4d8fe0;
  --sky:#dbe8f8;
  --white:#ffffff;
  --ink:#2b3440;
  --muted:#7a8594;
  --field:#e9eef5;
}
*{box-sizing:border-box;margin:0;padding:0}
html,body{width:1200px;height:2208px;overflow:hidden}
body{font-family:"Open Sans",Arial,sans-serif;color:var(--ink);background:var(--white);position:relative}
.abs{position:absolute}

/* header */
.site-header{position:absolute;top:0;left:0;width:1200px;height:112px;background:var(--white)}
.brand{position:absolute;left:70px;top:14px;text-align:center}
.brand-mark{font-family:"Montserrat",sans-serif;font-weight:800;font-size:54px;color:var(--blue);line-height:1;letter-spacing:2px}
.brand-name{font-family:"Montserrat",sans-serif;font-weight:800;font-size:13px;color:var(--blue);letter-spacing:1.5px;margin-top:6px}
.call{position:absolute;right:70px;top:28px;display:flex;align-items:center;gap:12px}
.call-icon{width:44px;height:44px;border-radius:50%;border:2px solid var(--blue);display:flex;align-items:center;justify-content:center}
.call-label{font-size:15px;color:var(--muted)}
.call-number{font-size:24px;color:var(--blue);font-weight:600;line-height:1.1}

.main-nav{position:absolute;top:112px;left:0;width:1200px;height:48px;background:var(--blue);display:flex;justify-content:center}
.main-nav a{display:block;width:150px;text-align:center;line-height:48px;color:var(--white);font-size:13px;font-weight:600;letter-spacing:1px;text-decoration:none}
.main-nav a.active{background:var(--blue-dark);border-bottom:3px solid var(--white)}

/* hero */
.hero{position:absolute;top:160px;left:0;width:1200px;height:1000px;background:var(--blue);overflow:hidden}
.hero-photo{position:absolute;left:0;top:0;width:1200px;height:720px;background:linear-gradient(180deg,#3f7fcf 0%,#2a6bc0 45%,#1a5fb4 100%)}
.hero-kicker{position:absolute;top:40px;width:100%;text-align:center;color:var(--white);font-family:"Montserrat",sans-serif;font-weight:500;font-size:40px}
.hero-title{position:absolute;top:88px;width:100%;text-align:center;color:var(--white);font-family:"Montserrat",sans-serif;font-weight:800;font-size:72px;letter-spacing:2px}
.hero-shape{position:absolute;left:0;top:0}
.services-hub{position:absolute;left:510px;top:410px;width:180px;height:180px;border-radius:50%;background:var(--blue);border:8px solid var(--white);box-shadow:0 6px 18px rgba(0,0,0,.25);display:flex;flex-direction:column;align-items:center;justify-content:center;color:var(--white);font-family:"Montserrat",sans-serif;font-weight:700}
.services-hub .hub-mark{font-size:44px;line-height:1}
.services-hub .hub-label{font-size:16px;letter-spacing:2px;margin-top:6px}
.service-icon{position:absolute;width:76px;height:76px;border-radius:50%;background:var(--white);box-shadow:0 4px 14px rgba(26,95,180,.25);display:flex;align-items:center;justify-content:center}
.service-label{position:absolute;font-family:"Marcellus",serif;font-size:20px;color:var(--ink);line-height:1.25}

/* about */
.about{position:absolute;top:1160px;left:0;width:1200px;height:320px;background:var(--blue);text-align:center;color:var(--white)}
.section-title{font-family:"Marcellus",serif;font-size:54px;font-weight:400}
.about .section-title{margin-top:10px}
.about p{width:920px;margin:18px auto 0;font-size:14px;line-height:1.7;color:var(--sky)}
.btn-light{display:inline-block;margin-top:28px;padding:12px 36px;border-radius:30px;background:var(--white);color:var(--blue);font-weight:700;font-size:14px;letter-spacing:1px}

/* contact */
.contact{position:absolute;top:1480px;left:0;width:1200px;height:430px;background:var(--white)}
.contact .section-title{text-align:center;color:var(--blue);margin-top:34px}
.contact-form{position:absolute;left:70px;top:130px;width:690px}
.contact-intro{font-family:"Marcellus",serif;font-size:20px;margin-bottom:18px}
.form-grid{display:grid;grid-template-columns:220px 220px 190px;gap:14px 20px;align-items:start}
.field{height:44px;border-radius:6px;background:var(--field);color:var(--muted);font-size:13px;padding:0 16px;line-height:44px}
.field.message{grid-column:1 / 3;height:76px}
.btn-submit{height:44px;border-radius:22px;background:var(--blue);color:var(--white);font-weight:700;font-size:16px;letter-spacing:1px;text-align:center;line-height:44px}
.contact-details{position:absolute;left:820px;top:130px;width:320px}
.contact-details h3{font-family:"Marcellus",serif;font-weight:400;font-size:20px;letter-spacing:1px;margin-bottom:18px}
.detail{display:flex;gap:12px;align-items:flex-start;font-size:13px;color:var(--muted);margin-bottom:12px;line-height:1.45}
.detail svg{flex:none;margin-top:2px}
.social{display:flex;gap:10px;margin-top:8px}
.social span{width:38px;height:38px;border-radius:50%;background:var(--blue);display:block}

/* footer */
.site-footer{position:absolute;top:1910px;left:0;width:1200px;height:298px;background:var(--blue);color:var(--white)}
.to-top{position:absolute;left:560px;top:70px;width:80px;height:80px;border-radius:50%;background:var(--blue-dark);border:6px solid var(--blue-light);display:flex;align-items:center;justify-content:center}
.footer-nav{position:absolute;top:190px;left:70px;width:1060px;display:flex;justify-content:center;border-bottom:1px solid rgba(255,255,255,.3);padding-bottom:14px}
.footer-nav a{width:150px;text-align:center;color:var(--sky);font-size:12px;letter-spacing:1px;text-decoration:none}
.copyright{position:absolute;bottom:0;left:0;width:100%;height:48px;line-height:48px;text-align:center;font-size:12px;color:var(--sky);background:var(--blue-deep);letter-spacing:.5px}
</style>
</head>
<body>

<header class="site-header">
  <div class="brand">
    <div class="brand-mark">QRN</div>
    <div class="brand-name">QUORRA HEALTH NETWORK LLC</div>
  </div>
  <div class="call">
    <div class="call-icon">
      <svg width="22" height="22" viewBox="0 0 24 24"><path d="M6.6 10.8a15 15 0 0 0 6.6 6.6l2.2-2.2a1 1 0 0 1 1-.25 11.4 11.4 0 0 0 3.6.57 1 1 0 0 1 1 1V20a1 1 0 0 1-1 1A17 17 0 0 1 3 4a1 1 0 0 1 1-1h3.5a1 1 0 0 1 1 1c0 1.25.2 2.45.57 3.57a1 1 0 0 1-.25 1z" fill="#1a5fb4"/></svg>
    </div>
    <div>
      <div class="call-label">Call Today</div>
      <div class="call-number">555 014 3386</div>
    </div>
  </div>
</header>

<nav class="main-nav">
  <a class="active" href="#">HOME</a>
  <a href="#">ABOUT</a>
  <a href="#">SERVICES</a>
  <a href="#">OUR TEAM</a>
  <a href="#">GET A QUOTE</a>
  <a href="#">CONTACT</a>
</nav>

<section class="hero">
  <div class="hero-photo" role="img" aria-label="Diverse team of doctors and healthcare staff working together, tinted blue"></div>
  <div class="hero-kicker">We Create Value</div>
  <div class="hero-title">&amp; BUILD CONFIDENCE</div>
  <svg class="hero-shape" width="1200" height="1000" viewBox="0 0 1200 1000">
    <path d="M0 640 C300 520 900 520 1200 640 L1200 900 C900 1010 300 1010 0 900 Z" fill="#ffffff"/>
  </svg>

  <div class="services-hub">
    <div class="hub-mark">QRN</div>
    <div class="hub-label">SERVICES</div>
  </div>

  <div class="service-icon" style="left:300px;top:640px">
    <svg width="40" height="40" viewBox="0 0 40 40" fill="none" stroke="#1a5fb4" stroke-width="2.5"><rect x="4" y="8" width="32" height="22" rx="2"/><path d="M12 24v-6M20 24v-10M28 24v-4"/><path d="M14 34h12"/></svg>
  </div>
  <div class="service-label" style="left:80px;top:650px;width:210px">Revenue Cycle<br>Management</div>

  <div class="service-icon" style="left:350px;top:770px">
    <svg width="40" height="40" viewBox="0 0 40 40" fill="none" stroke="#1a5fb4" stroke-width="2.5"><rect x="6" y="6" width="22" height="28" rx="2"/><path d="M11 14h12M11 20h12M11 26h7"/><path d="M30 12v18M26 21h8"/></svg>
  </div>
  <div class="service-label" style="left:110px;top:792px;width:240px">Medical Billing &amp; Coding</div>

  <div class="service-icon" style="left:562px;top:830px">
    <svg width="40" height="40" viewBox="0 0 40 40" fill="none" stroke="#1a5fb4" stroke-width="2.5"><rect x="8" y="7" width="24" height="29" rx="2"/><rect x="15" y="4" width="10" height="6" rx="1"/><path d="M14 22l4 4 8-9"/></svg>
  </div>
  <div class="service-label" style="left:480px;top:918px;width:240px;text-align:center">Regulatory Compliance</div>

  <div class="service-icon" style="left:770px;top:770px">
    <svg width="40" height="40" viewBox="0 0 40 40" fill="#1a5fb4"><circle cx="20" cy="13" r="5"/><circle cx="9" cy="16" r="4"/><circle cx="31" cy="16" r="4"/><path d="M11 32c0-6 4-10 9-10s9 4 9 10z"/><path d="M2 31c0-5 3-8 7-8 1.5 0 2.5.4 3.5 1-1.6 2-2.5 4.5-2.5 7z"/><path d="M38 31c0-5-3-8-7-8-1.5 0-2.5.4-3.5 1 1.6 2 2.5 4.5 2.5 7z"/></svg>
  </div>
  <div class="service-label" style="left:862px;top:792px;width:260px">Human Resources Training</div>

  <div class="service-icon" style="left:820px;top:640px">
    <svg width="40" height="40" viewBox="0 0 40 40" fill="none" stroke="#1a5fb4" stroke-width="2.5"><rect x="5" y="6" width="30" height="20" rx="1"/><path d="M20 26v8M13 34h14"/><path d="M11 20l6-6 4 4 7-7"/></svg>
  </div>
  <div class="service-label" style="left:912px;top:650px;width:220px">Staff Education<br>and Training</div>
</section>

<section class="about">
  <h2 class="section-title">About Us</h2>
  <p>We partner with physician practices to handle the business side of medicine, from billing and coding to compliance and staffing. Our team brings years of healthcare expertise, clear reporting and steady support, so doctors can spend less time on paperwork and more time caring for patients in their community every day.</p>
  <span class="btn-light">LEARN MORE</span>
</section>

<section class="contact">
  <h2 class="section-title">Contact Us</h2>
  <div class="contact-form">
    <div class="contact-intro">We look forward to hearing from you.</div>
    <div class="form-grid">
      <div class="field">Name</div>
      <div class="field">Company Info</div>
      <div class="btn-submit">SUBMIT</div>
      <div class="field">Phone</div>
      <div class="field">E-Mail</div>
      <div></div>
      <div class="field message">Message</div>
    </div>
  </div>
  <div class="contact-details">
    <h3>CONTACT DETAILS</h3>
    <div class="detail">
      <svg width="16" height="18" viewBox="0 0 24 24"><path d="M12 2a7 7 0 0 0-7 7c0 5 7 13 7 13s7-8 7-13a7 7 0 0 0-7-7zm0 9.5A2.5 2.5 0 1 1 12 6.5a2.5 2.5 0 0 1 0 5z" fill="#1a5fb4"/></svg>
      <span>Northgate Office Services LLC<br>P.O. Box 2210, Trenton, NJ 08601</span>
    </div>
    <div class="detail">
      <svg width="16" height="16" viewBox="0 0 24 24"><path d="M6.6 10.8a15 15 0 0 0 6.6 6.6l2.2-2.2a1 1 0 0 1 1-.25 11.4 11.4 0 0 0 3.6.57 1 1 0 0 1 1 1V20a1 1 0 0 1-1 1A17 17 0 0 1 3 4a1 1 0 0 1 1-1h3.5a1 1 0 0 1 1 1c0 1.25.2 2.45.57 3.57a1 1 0 0 1-.25 1z" fill="#1a5fb4"/></svg>
      <span>(555) 014-2290</span>
    </div>
    <div class="detail">
      <svg width="16" height="16" viewBox="0 0 24 24"><path d="M6.6 10.8a15 15 0 0 0 6.6 6.6l2.2-2.2a1 1 0 0 1 1-.25 11.4 11.4 0 0 0 3.6.57 1 1 0 0 1 1 1V20a1 1 0 0 1-1 1A17 17 0 0 1 3 4a1 1 0 0 1 1-1h3.5a1 1 0 0 1 1 1c0 1.25.2 2.45.57 3.57a1 1 0 0 1-.25 1z" fill="#1a5fb4"/></svg>
      <span>(555) 014-2291</span>
    </div>
    <div class="detail">
      <svg width="16" height="14" viewBox="0 0 24 20"><rect x="1" y="1" width="22" height="18" rx="2" fill="none" stroke="#1a5fb4" stroke-width="2"/><path d="M2 3l10 8 10-8" fill="none" stroke="#1a5fb4" stroke-width="2"/></svg>
      <span>hello@quorrahealth.com</span>
    </div>
    <div class="social"><span></span><span></span><span></span><span></span></div>
  </div>
</section>

<footer class="site-footer">
  <svg class="abs" style="left:0;top:0" width="1200" height="110" viewBox="0 0 1200 110">
    <path d="M0 0 H1200 V10 C900 110 300 110 0 10 Z" fill="#ffffff"/>
  </svg>
  <div class="to-top">
    <svg width="26" height="26" viewBox="0 0 24 24" fill="none" stroke="#ffffff" stroke-width="2.5"><path d="M6 13l6-6 6 6M6 19l6-6 6 6"/></svg>
  </div>
  <nav class="footer-nav">
    <a href="#">HOME</a>
    <a href="#">ABOUT</a>
    <a href="#">SERVICES</a>
    <a href="#">OUR TEAM</a>
    <a href="#">GET A QUOTE</a>
    <a href="#">CONTACT</a>
  </nav>
  <div class="copyright">© QUORRA HEALTH NETWORK LLC. 2018. All Rights Reserved.</div>
</footer>

</body>
</html>
```